Web Design Project

We are an IT System Integrator. We provide Korvin 450 ERP System, CRM etc. We also provide hardware, networking servicing. Please look at www.zolvantix.com.sg. They provide the same service as us. We like to redesign our web site. I will attached the color that I prefer for reference.

Our website is www.tadurk.com.sg.  It has been created about 14 years ago.  We are trying to revamp it with a new look and information.   The new website must be informative, fast.    I have attached an attachment which show the color that I prefer(brownish golden).   

Our competitor (www.zolvantix.com) is carrying the same trade as us.  They have all the informations In their website that we will like to have.  Therefore I recommend you to take a look at my competitor website and have a better   
understanding on the kind of information I would like to have for my new website.

This project is guarantee to the person with the best design.  We can have it guarantee.

Target Market(s)

Corporate and companies

Industry/Entity Type

Hardware

```html
<!DOCTYPE html>
<html lang="en">
<head>
<meta charset="utf-8">
<title>Tadurk Information Systems</title>
<link href="https://fonts.googleapis.com/css2?family=Roboto:wght@400;500;700&display=swap" rel="stylesheet">
<style>
:root{
  --gold:#a57d2c;
  --gold-dark:#7c5a1a;
  --gold-light:#d8b66a;
  --brown:#6e5018;
  --cream:#f2ead5;
  --cream-dark:#dccfa8;
  --tan:#cfc19b;
  --steel:#8c9296;
  --ink:#333;
  --white:#fff;
  --card:#f1f1f1;
  --orange:#e2a24a;
}
*{box-sizing:border-box;margin:0;padding:0}
html,body{width:884px;height:1200px;overflow:hidden}
body{font-family:'Roboto',sans-serif;position:relative;background:var(--cream);color:var(--ink)}
.abs{position:absolute}
.site-header{left:0;top:0;width:884px;height:116px;background:radial-gradient(ellipse at 190px 20px,#f7e6b5 0,#c9a65b 30%,var(--gold) 60%,#8d6a24 100%)}
.brand{left:106px;top:36px;display:flex;align-items:center;gap:10px}
.brand-name{font-size:40px;font-weight:700;color:#f3d98e;letter-spacing:1px}
.brand-dot{width:26px;height:26px;border-radius:50%;background:#f3d98e}
.top-links{left:440px;top:21px;width:194px;font-size:10px;color:var(--white);display:flex;justify-content:flex-end;gap:8px;white-space:nowrap}
.search{left:643px;top:17px;width:112px;height:19px;border-radius:10px;background:var(--white);font-size:9px;color:#666;padding:4px 11px}
.search-icon{left:759px;top:17px}
.main-nav{left:322px;top:60px;width:464px;height:29px;background:var(--white);border-radius:3px;display:flex;align-items:center;font-size:11px;color:var(--brown);white-space:nowrap}
.nav-home{flex:none;width:38px;height:29px;background:linear-gradient(#e6b45b,#c98b2a);border-radius:3px 0 0 3px;display:flex;align-items:center;justify-content:center}
.nav-items{flex:1;display:flex;justify-content:space-evenly;align-items:center}
.main-nav span.sep{color:#999}
.stripe{left:0;width:884px;height:12px;background:repeating-linear-gradient(45deg,#7d8387 0 2px,#a3a9ad 2px 4px)}
.hero-band{left:0;top:128px;width:884px;height:310px;background:radial-gradient(#8a6a26 1px,transparent 1px) 0 0/4px 4px,linear-gradient(#a8822f,#8f6d24)}
.hero-frame{left:97px;top:129px;width:694px;height:308px;background:#c4a150}
.hero-photo{left:103px;top:135px;width:682px;height:296px;background:linear-gradient(120deg,#5b4a36 0,#b5a793 30%,#e3dccf 55%,#a8947a 80%,#6b5a48 100%)}
.hero-caption{left:103px;top:255px;width:351px;height:80px;background:rgba(20,15,8,.8);color:var(--white);padding:16px 24px}
.hero-caption h2{font-size:20px;font-weight:500;margin-bottom:5px}
.hero-caption p{font-size:12px}
.dots{display:flex;gap:4px}
.dot{width:6px;height:6px;border-radius:50%;background:var(--white)}
.dot.on{background:#5ab0c8}
.quote{left:623px;top:212px;width:162px;height:178px;background:#fbecc6;padding:12px 16px;font-size:12px;color:#3a2a0a}
.quote-head{left:623px;top:177px;width:176px;height:36px;background:linear-gradient(#d6a448,#a77520);color:var(--white);font-size:16px;padding:5px 5px;white-space:nowrap}
.quote-head b{font-size:24px;font-weight:700}
.quote label{display:block;margin-bottom:2px;font-weight:500}
.quote .field{width:119px;height:15px;background:var(--white);border:1px solid #999;border-radius:3px;margin-bottom:6px}
.send{margin-top:6px;width:74px;height:20px;border-radius:10px;background:linear-gradient(#e6c06a,#b38530);color:var(--white);text-align:center;font-size:12px;line-height:20px}
.content-band{left:0;top:440px;width:884px;height:442px;background:repeating-linear-gradient(45deg,#f4edd9 0 2px,#ece3c9 2px 4px)}
.card{top:462px;width:162px;height:175px;background:var(--card);border:1px solid #ddd;box-shadow:0 6px 6px -4px rgba(0,0,0,.25)}
.card-logo{height:84px;display:flex;align-items:center;justify-content:center;border-bottom:3px solid var(--brown);font-weight:700}
.card h3{font-size:12px;font-weight:700;color:var(--brown);padding:8px 6px 3px}
.card p,.body-text{font-size:8.2px;line-height:10px;color:#444;padding:0 6px}
.panel{background:var(--white);border:1px solid #ccc;box-shadow:0 6px 6px -4px rgba(0,0,0,.25)}
.panel-head{height:32px;background:linear-gradient(#d1ad60,#a98131);color:var(--white);font-size:14px;font-weight:500;padding:8px 21px}
.portrait{left:105px;top:708px;width:168px;height:142px;background:#111;border:4px solid #e5e5e5}
.hello{left:283px;top:712px;font-size:22px;font-weight:400;color:#222}
.readmore{left:280px;top:834px;width:62px;height:17px;background:var(--gold-dark);color:var(--white);font-size:9px;text-align:center;line-height:17px}
.news-photo{left:616px;top:703px;width:169px;height:67px;background:linear-gradient(90deg,#d8d8d8,#f0f0f0 40%,#9a9a9a)}
.partners-band{left:0;top:882px;width:884px;height:103px;background:var(--tan)}
.badge{top:927px;width:110px;height:46px}
.badge.green{background:#1e8a66}
.badge.black{background:#111}
.footer{left:0;top:993px;width:884px;height:207px;background:linear-gradient(var(--brown),#8e6c27 50%,#6e5018)}
.col{top:1013px;font-size:8px;line-height:13.3px;color:#f0e2bd;white-space:nowrap}
.col h4{font-size:9px;font-weight:700;color:var(--white);letter-spacing:.5px;margin-bottom:6px}
.newsletter{left:100px;top:1012px;width:155px;height:24px;border:3px solid #aaa;background:var(--white);font-size:8px;color:#666;padding:4px 8px}
.social{top:1046px;width:25px;height:25px}
.company{left:103px;top:1080px;font-size:8.5px;line-height:13px;color:var(--white);font-style:normal}
.company strong{font-size:12px;display:block;margin-bottom:1px}
.rule{left:0;top:1169px;width:884px;height:1px;background:#b79a5a}
.legal{top:1183px;font-size:7px;color:var(--white);white-space:nowrap}
</style>
</head>
<body>
<header class="abs site-header">
  <div class="abs brand"><span class="brand-name">Tadurk</span><span class="brand-dot"></span></div>
  <div class="abs top-links"><span>• FAQ</span><span>• Resources</span><span>• Log Incident</span></div>
  <div class="abs search">Search</div>
  <svg class="abs search-icon" width="18" height="18" viewBox="0 0 18 18"><circle cx="10" cy="7" r="5.5" fill="none" stroke="#fff" stroke-width="2"/><line x1="6" y1="11" x2="1.5" y2="16" stroke="#fff" stroke-width="2"/></svg>
  <nav class="abs main-nav">
    <span class="nav-home"><svg width="14" height="12" viewBox="0 0 14 12"><path d="M7 0L0 6h2v6h4V8h2v4h4V6h2z" fill="#fff"/></svg></span>
    <span class="nav-items"><span>Solutions</span><span class="sep">|</span><span>Hardware</span><span class="sep">|</span><span>Services</span><span class="sep">|</span><span>Clients</span><span class="sep">|</span><span>About Us</span><span class="sep">|</span><span>Contact Us</span></span>
  </nav>
</header>
<div class="abs stripe" style="top:116px"></div>

<section class="abs hero-band"></section>
<div class="abs hero-frame"></div>
<div class="abs hero-photo" role="img" aria-label="Warehouse shelving stacked with boxes and a worker with a handheld terminal"></div>
<div class="abs hero-caption"><h2>Warehouse Management</h2><p>Achieve warehouse visibility and maximize its storage</p></div>
<div class="abs dots" style="left:112px;top:419px"><span class="dot"></span><span class="dot on"></span><span class="dot"></span><span class="dot"></span><span class="dot"></span></div>
<form class="abs quote">
  <div style="height:2px"></div>
  <label>Name</label><div class="field"></div>
  <label>Mobile number</label><div class="field"></div>
  <label>Email</label><div class="field"></div>
  <div class="send">SEND</div>
</form>
<div class="abs quote-head">Get a <b>FREE</b> Quote</div>

<section class="abs content-band"></section>
<article class="abs card" style="left:96px">
  <div class="card-logo" style="color:#0e5c45;font-size:34px">Korvin</div>
  <h3>Korvin Certified</h3>
  <p>Lorem ipsum dolor sit amet, consectetur adipiscing elit. Integer id dolor magna. Aliquam elit metus, laoreet et mattis eu, bibendum ac risus. Pellentesque odio nisi, iaculis eget ornare et, pulvinar eget</p>
</article>
<article class="abs card" style="left:273px">
  <div class="card-logo"><svg width="80" height="44" viewBox="0 0 80 44"><rect x="2" y="4" width="30" height="18" rx="3" fill="none" stroke="#333" stroke-width="2.5"/><path d="M8 22v7l6-7" fill="none" stroke="#333" stroke-width="2.5"/><rect x="30" y="10" width="46" height="26" rx="4" fill="#fff" stroke="#333" stroke-width="2.5"/><path d="M38 36l-6 8 12-8" fill="#fff" stroke="#333" stroke-width="2.5"/><circle cx="43" cy="23" r="2.5" fill="#333"/><circle cx="53" cy="23" r="2.5" fill="#333"/><circle cx="63" cy="23" r="2.5" fill="#333"/><circle cx="11" cy="13" r="1.8" fill="#333"/><circle cx="17" cy="13" r="1.8" fill="#333"/><circle cx="23" cy="13" r="1.8" fill="#333"/></svg></div>
  <h3>Success Stories</h3>
  <p>Lorem ipsum dolor sit amet, consectetur adipiscing elit. Integer id dolor magna. Aliquam elit metus, laoreet et mattis eu, bibendum ac risus. Pellentesque odio nisi, iaculis eget ornare et, pulvinar eget</p>
</article>
<article class="abs card" style="left:449px">
  <div class="card-logo" style="color:#1d5aa6;font-size:32px">Lumara</div>
  <h3>Latest Lumara</h3>
  <p>Lorem ipsum dolor sit amet, consectetur adipiscing elit. Integer id dolor magna. Aliquam elit metus, laoreet et mattis eu, bibendum ac risus. Pellentesque odio nisi, iaculis eget ornare et, pulvinar eget</p>
</article>
<article class="abs card" style="left:626px">
  <div class="card-logo"><svg width="62" height="48" viewBox="0 0 62 48"><g fill="#7b6444"><circle cx="22" cy="20" r="12"/><g stroke="#7b6444" stroke-width="7"><line x1="22" y1="3" x2="22" y2="37"/><line x1="5" y1="20" x2="39" y2="20"/><line x1="10" y1="8" x2="34" y2="32"/><line x1="34" y1="8" x2="10" y2="32"/></g><circle cx="46" cy="34" r="7"/><g stroke="#7b6444" stroke-width="4"><line x1="46" y1="24" x2="46" y2="44"/><line x1="36" y1="34" x2="56" y2="34"/><line x1="39" y1="27" x2="53" y2="41"/><line x1="53" y1="27" x2="39" y2="41"/></g></g><circle cx="22" cy="20" r="5" fill="#f1f1f1"/><circle cx="46" cy="34" r="3" fill="#f1f1f1"/></svg></div>
  <h3>Services Beyond</h3>
  <p>Lorem ipsum dolor sit amet, consectetur adipiscing elit. Integer id dolor magna. Aliquam elit metus, laoreet et mattis eu, bibendum ac risus. Pellentesque odio nisi, iaculis eget ornare et, pulvinar eget</p>
</article>

<section class="abs panel" style="left:97px;top:659px;width:456px;height:201px">
  <div class="panel-head">About Us</div>
</section>
<div class="abs portrait" role="img" aria-label="Portrait photo of a company representative"></div>
<h2 class="abs hello">Hello there !</h2>
<p class="abs body-text" style="left:278px;top:748px;width:266px">Lorem ipsum dolor sit amet, consectetur adipiscing elit. Integer id dolor magna. Aliquam elit metus, laoreet et mattis eu, bibendum ac risus. Pellentesque odio nisi, iaculis eget ornare et, pulvinar eget nibh. Nunc a arcu augue. Cras hendrerit tincidunt ligula a porta. Maecenas scelerisque tortor arcu, ac porta lorem auctor id. Quisque aliquam ipsum ut enim malesuada, nec fringilla nunc dictum.</p>
<div class="abs readmore">readmore</div>

<section class="abs panel" style="left:567px;top:659px;width:223px;height:201px">
  <div class="panel-head" style="padding-left:15px">Latest News</div>
</section>
<div class="abs dots" style="left:725px;top:672px"><span class="dot"></span><span class="dot on"></span><span class="dot"></span><span class="dot"></span><span class="dot"></span></div>
<svg class="abs" style="left:576px;top:703px" width="34" height="36" viewBox="0 0 34 36"><rect x="1" y="3" width="32" height="32" fill="#fff" stroke="#a57d2c" stroke-width="2"/><rect x="1" y="3" width="32" height="6" fill="#a57d2c"/><rect x="7" y="0" width="3" height="7" fill="#7c5a1a"/><rect x="24" y="0" width="3" height="7" fill="#7c5a1a"/><text x="17" y="29" text-anchor="middle" font-family="Roboto,sans-serif" font-size="17" font-weight="700" fill="#222">3</text></svg>
<div class="abs" style="left:576px;top:742px;width:34px;text-align:center;font-size:8px;font-weight:700;line-height:11px">JULY<br>2013</div>
<div class="abs news-photo" role="img" aria-label="Business team meeting around a laptop"></div>
<h3 class="abs" style="left:577px;top:786px;font-size:12px;font-weight:700;color:#111">HEADER TITLE HERE</h3>
<p class="abs body-text" style="left:571px;top:808px;width:212px">Lorem ipsum dolor sit amet, consectetur adipiscing elit. Integer id dolor magna. Aliquam elit metus, laoreet et mattis eu, bibendum ac risus. Pellentesque odio nisi, iaculis eget ornare et, pulvinar eget nibh. Nunc a arcu</p>

<section class="abs partners-band"></section>
<h2 class="abs" style="left:110px;top:893px;font-size:14px;font-weight:500;color:var(--gold-dark)">Partners</h2>
<svg class="abs" style="left:104px;top:932px" width="16" height="36" viewBox="0 0 16 36"><path d="M14 1L2 18l12 17" fill="none" stroke="#8a7a55" stroke-width="1.5"/></svg>
<svg class="abs" style="left:767px;top:932px" width="16" height="36" viewBox="0 0 16 36"><path d="M2 1l12 17L2 35" fill="none" stroke="#8a7a55" stroke-width="1.5"/></svg>
<div class="abs badge green" style="left:138px"></div>
<div class="abs badge black" style="left:260px"></div>
<div class="abs badge green" style="left:383px"></div>
<div class="abs badge black" style="left:509px"></div>
<div class="abs badge green" style="left:633px"></div>
<div class="abs stripe" style="top:984px;height:9px"></div>

<footer class="abs footer"></footer>
<div class="abs newsletter">Enter e-mail for newsletter</div>
<svg class="abs" style="left:236px;top:1018px" width="12" height="12" viewBox="0 0 12 12"><circle cx="6" cy="6" r="6" fill="#555"/><path d="M5 3l3 3-3 3" fill="none" stroke="#fff" stroke-width="1.5"/></svg>
<div class="abs social" style="left:103px;background:#3b5998"></div>
<div class="abs social" style="left:130px;background:#777"></div>
<div class="abs social" style="left:157px;background:#999"></div>
<div class="abs social" style="left:186px;background:#999"></div>
<address class="abs company"><strong>Tadurk Information Systems</strong>Rue des Tilleuls 12 - 4821<br>Ostrevelle - Belgium<br>Phone: +32 (0)61 45 90 12<br>Fax: +32 (0)61 45 90 13</address>
<div class="abs col" style="left:280px"><h4>SOLUTIONS</h4>Korvin ERP Lumara<br>Financial Management<br>Korvin ERP Lumara<br>Financial Management<br>Korvin ERP Lumara<br>Financial Management</div>
<div class="abs col" style="left:392px"><h4>HARDWARE</h4>Submenu item 1<br>Submenu item 2<br>Submenu item 3<br>Submenu item 4<br>Submenu item 5<br>Submenu item 6</div>
<div class="abs col" style="left:473px"><h4>SERVICES</h4>Submenu item 1<br>Submenu item 2<br>Submenu item 3<br>Submenu item 4<br>Submenu item 5<br>Submenu item 6</div>
<div class="abs col" style="left:555px"><h4>CLIENTS</h4>Submenu item 1<br>Submenu item 2<br>Submenu item 3<br>Submenu item 4<br>Submenu item 5<br>Submenu item 6</div>
<div class="abs col" style="left:640px"><h4>ABOUT US</h4>Submenu item 1<br>Submenu item 2<br>Submenu item 3<br>Submenu item 4<br>Submenu item 5<br>Submenu item 6</div>
<div class="abs col" style="left:730px"><h4>CONTACT</h4>Inquiry<br>Location</div>
<div class="abs rule"></div>
<div class="abs legal" style="left:103px">Copyright Brightwell Systems. All rights reserved.</div>
<div class="abs legal" style="left:655px">Terms &amp; Conditions &nbsp;| Privacy &nbsp;| Sitemap</div>
</body>
</html>
```